Mobile version of Desktop site

I need a mobile version of my desktop site. Up until now we have been using a mobile translation service but there are too many drawbacks and bugs. So I need a mobile site designed to be used on an iPhone or android phone that is "Inspired by" our desktop site. I am going to setup two completely separate sites, served either as desktop or mobile.

I have attached an eps version of my logo.

Design this site as though the largest screen it will be viewed on is an iPhone 6 plus, but more likely it will be viewed on smaller screens.

Phone number as a button to click to call should be prominent.

Just need a basic attorney website that is clean and has the look and feel of the desktop site, but readable and usable on a smartphone.

Base your design off of an inner page like whats on this url:
Desktop url: https://www.brackenfieldlaw.com/mesa-verdan.html

Reason: I am extending the deadline to allow for implementation of feedback

Target Market(s)

everyone

Industry/Entity Type

Attorney

Number of Pages Required

1 page

Font styles to use
Sans Serif

Requirements
Must have
• Must be readable and usable on a smart phone, from a 5.5" iPhone 6 plus on down to the original iPhone. I'm looking for usability and readability.
Nice to have
• I would like to see logos shown at the top filling the width of the page if viewed in portrait mode with the phone number next, and it should be a complementing version of my desktop site.
Should not have
• I do not want to see a lot of small details that would be lost on a smartphone platform.

```html
<!DOCTYPE html>
<html lang="en">
<head>
<meta charset="utf-8">
<title>Brackenfield Attorneys – Personal Injury Lawyer in Mesa Verdan</title>
<link rel="stylesheet" href="https://fonts.googleapis.com/css2?family=Roboto:wght@400;500;700&family=Bitter:wght@700&display=swap">
<style>
  :root {
    --navy: #0c2f5f;
    --navy-form: #0d3163;
    --field-line: #2c5c9c;
    --send: #e4532b;
    --ink: #2b2b2b;
    --white: #ffffff;
    --rule: #d9d9d9;
    --badge-navy: #1c3f73;
    --badge-grey: #e9e9e9;
  }
  * { box-sizing: border-box; margin: 0; padding: 0; }
  html, body {
    width: 1200px; height: 2413px; overflow: hidden;
    background: var(--white);
    font-family: "Roboto", Arial, sans-serif;
    color: var(--ink);
  }
  .page { position: relative; width: 1200px; height: 2413px; }

  .site-header {
    position: absolute; left: 0; top: 0; width: 1200px; height: 203px;
    display: flex; align-items: center; justify-content: space-between;
    padding: 0 32px 0 29px;
  }
  .brand-name {
    font-family: "Roboto", Arial, sans-serif;
    font-weight: 500; font-size: 60px; color: var(--navy);
    letter-spacing: 1px;
  }
  .menu-toggle { width: 84px; height: 76px; }

  .hero {
    position: absolute; left: 0; top: 203px; width: 1200px; height: 513px;
    background: linear-gradient(180deg, #3d3550 0%, #9a5a5f 30%, #e58a55 52%, #c3704c 60%, #2e2a33 80%, #5a4650 100%);
  }
  .hero-arrow { position: absolute; top: 200px; width: 70px; height: 110px; }
  .hero-arrow.prev { left: 70px; }
  .hero-arrow.next { right: 70px; }

  .share-row {
    position: absolute; top: 765px; left: 0; width: 1200px;
    display: flex; justify-content: center; gap: 58px;
  }
  .share-btn { display: flex; align-items: center; gap: 10px; }
  .share-btn .label {
    display: flex; align-items: center; gap: 8px;
    height: 56px; padding: 0 16px;
    border: 2px solid #c9c9c9; border-radius: 6px;
    font-size: 28px; font-weight: 500; color: #333; background: #f6f6f6;
  }
  .share-btn .label i { display: block; width: 26px; height: 26px; background: #8a8a8a; }
  .share-btn .count {
    height: 52px; padding: 0 14px; display: flex; align-items: center;
    border: 2px solid #c9c9c9; border-radius: 4px; font-size: 26px; color: #333;
  }

  .call-cta {
    position: absolute; top: 862px; left: 0; width: 1200px; text-align: center;
  }
  .call-cta .lead { font-size: 46px; color: #2e2e2e; }
  .call-cta .phone {
    display: inline-block; margin-top: 14px;
    font-size: 64px; font-weight: 500; color: var(--navy); text-decoration: none;
  }

  .contact-form {
    position: absolute; top: 1047px; left: 0; width: 1200px; height: 678px;
    background: var(--navy-form);
  }
  .contact-form h2 {
    position: absolute; top: 38px; width: 100%; text-align: center;
    font-size: 44px; font-weight: 500; color: var(--white); letter-spacing: 1px;
  }
  .field {
    position: absolute; border: 2px solid var(--field-line);
    color: var(--white); font-size: 34px; font-weight: 500;
    padding: 38px 0 0 42px; letter-spacing: 0.5px;
  }
  .field.name { left: 58px; top: 130px; width: 516px; height: 116px; padding-top: 36px; }
  .field.email { left: 618px; top: 130px; width: 514px; height: 116px; padding-top: 36px; }
  .field.description { left: 58px; top: 284px; width: 1074px; height: 249px; padding-top: 34px; }
  .send-btn {
    position: absolute; left: 893px; top: 557px; width: 241px; height: 92px;
    background: var(--send); color: var(--white);
    font-size: 38px; font-weight: 500; letter-spacing: 1px;
    display: flex; align-items: center; justify-content: center;
  }

  .affiliations {
    position: absolute; top: 1790px; left: 0; width: 1200px; height: 150px;
  }
  .badge { position: absolute; }
  .badge.accredited { left: 23px; top: 22px; width: 256px; height: 100px; background: var(--badge-navy); border-radius: 6px; }
  .badge.association { left: 313px; top: 16px; width: 194px; height: 112px; background: var(--badge-navy); }
  .badge.member { left: 541px; top: 0; width: 150px; height: 150px; border-radius: 50%; background: var(--badge-navy); }
  .badge.reviews { left: 783px; top: 8px; width: 380px; height: 154px; background: var(--badge-grey); border: 2px solid #cfcfcf; border-radius: 6px; }

  .page-title {
    position: absolute; top: 2010px; left: 32px;
    font-family: "Bitter", Georgia, serif; font-weight: 700;
    font-size: 49px; color: var(--navy);
  }
</style>
</head>
<body>
<div class="page">
  <header class="site-header">
    <div class="brand-name">Brackenfield Attorneys</div>
    <svg class="menu-toggle" viewBox="0 0 84 76" aria-label="Menu">
      <rect x="0" y="0" width="84" height="14" fill="#0c2f5f"/>
      <rect x="0" y="31" width="84" height="14" fill="#0c2f5f"/>
      <rect x="0" y="62" width="84" height="14" fill="#0c2f5f"/>
    </svg>
  </header>

  <div class="hero" role="img" aria-label="Sunset over a long ocean pier reflected on the wet beach">
    <svg class="hero-arrow prev" viewBox="0 0 70 110" aria-hidden="true">
      <polyline points="60,5 10,55 60,105" fill="none" stroke="#ffffff" stroke-opacity="0.75" stroke-width="10"/>
    </svg>
    <svg class="hero-arrow next" viewBox="0 0 70 110" aria-hidden="true">
      <polyline points="10,5 60,55 10,105" fill="none" stroke="#ffffff" stroke-opacity="0.75" stroke-width="10"/>
    </svg>
  </div>

  <div class="share-row">
    <div class="share-btn"><span class="label">Save</span></div>
    <div class="share-btn"><span class="label"><i></i>Share</span><span class="count">12</span></div>
    <div class="share-btn"><span class="label"><i></i>Like</span><span class="count">6</span></div>
    <div class="share-btn"><span class="label">+1</span><span class="count">1.2k</span></div>
  </div>

  <div class="call-cta">
    <p class="lead">Call Now For a Free Consultation</p>
    <a class="phone" href="tel:5550142870">(555)014-2870</a>
  </div>

  <section class="contact-form">
    <h2>HOW CAN WE HELP YOU</h2>
    <div class="field name">NAME</div>
    <div class="field email">EMAIL</div>
    <div class="field description">DESCRIPTION</div>
    <div class="send-btn">SEND</div>
  </section>

  <div class="affiliations">
    <div class="badge accredited" role="img" aria-label="Accredited business badge"></div>
    <div class="badge association" role="img" aria-label="Trial lawyers association badge"></div>
    <div class="badge member" role="img" aria-label="Consumer attorneys member seal"></div>
    <div class="badge reviews" role="img" aria-label="Customer reviews listing"></div>
  </div>

  <h1 class="page-title">Personal Injury Lawyer in Mesa Verdan</h1>
</div>
</body>
</html>
```